Customer Value Leaflet

We need a bi-fold brochure designing, based on the attached PDF wireframes. Our company name is brambleharvik.com (of which the logo is currently being designed). The corporate colour is orange (the exact shade of which we are happy to leave to the designers discretion).

The leaflet will distributed to customer experience experts and marketers so the design needs to be bright, engaging, clean and simple. Design is critical.

It Company

```html
<!DOCTYPE html>
<html lang="en">
<head>
<meta charset="utf-8">
<title>Customer Value – Kim and Kevin timeline</title>
<link rel="stylesheet" href="https://fonts.googleapis.com/css2?family=PT+Sans:wght@400&display=swap">
<style>
  :root {
    --ink: #1f1f1f;
    --icon: #5a5a5a;
    --icon-soft: #8a8a8a;
    --timeline: #a9a9a9;
    --paper: #ffffff;
    --brand-orange: #f7941d;
  }
  * { box-sizing: border-box; margin: 0; padding: 0; }
  html, body { width: 1200px; height: 1200px; overflow: hidden; background: var(--paper); }
  body { font-family: "PT Sans", "Myriad Pro", Arial, sans-serif; color: var(--ink); }
  .leaflet { position: relative; width: 1200px; height: 1200px; background: var(--paper); }

  .timeline { position: absolute; left: 0; top: 0; width: 1200px; height: 1000px; }
  .timeline-label {
    position: absolute; left: 613px; width: 300px; margin-left: -150px;
    transform: rotate(-90deg); text-align: center;
    font-size: 32px; letter-spacing: 2px; color: var(--paper); line-height: 40px;
  }

  .story { position: absolute; text-align: center; font-size: 34px; line-height: 48px; width: 520px; margin-left: -260px; }
  .icon { position: absolute; }
  .icon-placeholder { border-radius: 50%; }

  .verdict {
    position: absolute; left: 0; top: 998px; width: 1200px; height: 202px;
    background: var(--brand-orange);
    display: flex; align-items: center; justify-content: center;
    font-size: 40px; color: var(--ink);
  }
</style>
</head>
<body>
<main class="leaflet">

  <svg class="timeline" viewBox="0 0 1200 1000" aria-hidden="true">
    <rect x="571" y="0" width="85" height="282" fill="var(--timeline)"/>
    <rect x="571" y="298" width="85" height="333" fill="var(--timeline)"/>
    <path d="M571 647 H656 V857 H720 L613 988 L504 857 H571 Z" fill="var(--timeline)"/>
  </svg>
  <div class="timeline-label" style="top:120px">+ 1 WEEK</div>
  <div class="timeline-label" style="top:444px">+ 1 MONTH</div>
  <div class="timeline-label" style="top:807px">+ 6 MONTHS</div>

  <!-- Kim -->
  <p class="story" style="left:353px; top:32px">Kim calls you to return<br>an item…</p>
  <div class="icon icon-placeholder" role="img" aria-label="Customer service agent with headset"
       style="left:293px; top:128px; width:120px; height:120px; background: radial-gradient(circle, #9a9a9a, #5a5a5a);"></div>

  <p class="story" style="left:353px; top:348px">places 4 more online<br>orders…</p>
  <svg class="icon cart-icon" viewBox="0 0 120 100" style="left:262px; top:432px; width:130px; height:108px" aria-label="Shopping cart" role="img">
    <path d="M4 10 H20 L36 70 H104" fill="none" stroke="var(--icon)" stroke-width="6" stroke-linecap="round" stroke-linejoin="round"/>
    <path d="M24 22 H114 L104 60 H34 Z" fill="var(--icon)"/>
    <g fill="var(--paper)">
      <circle cx="40" cy="33" r="5"/><circle cx="56" cy="33" r="5"/><circle cx="72" cy="33" r="5"/><circle cx="88" cy="33" r="5"/><circle cx="104" cy="33" r="5"/>
      <circle cx="46" cy="49" r="5"/><circle cx="62" cy="49" r="5"/><circle cx="78" cy="49" r="5"/><circle cx="94" cy="49" r="5"/>
    </g>
    <circle cx="44" cy="86" r="8" fill="var(--icon)"/><circle cx="96" cy="86" r="8" fill="var(--icon)"/>
  </svg>

  <p class="story" style="left:353px; top:665px">then places another<br>order but doesn’t come<br>back for a month</p>
  <svg class="icon stop-icon" viewBox="0 0 100 100" style="left:278px; top:802px; width:130px; height:130px" role="img" aria-label="Stop sign">
    <polygon points="30,2 70,2 98,30 98,70 70,98 30,98 2,70 2,30" fill="#444"/>
    <rect x="36" y="26" width="28" height="46" rx="10" fill="var(--paper)"/>
  </svg>

  <!-- Kevin -->
  <p class="story" style="left:888px; top:32px">Kevin makes another<br>purchase…</p>
  <svg class="icon basket-icon" viewBox="0 0 120 90" style="left:785px; top:150px; width:150px; height:112px" role="img" aria-label="Shopping basket">
    <path d="M34 34 L52 6" fill="none" stroke="var(--icon)" stroke-width="6" stroke-linecap="round"/>
    <rect x="4" y="32" width="112" height="12" rx="3" fill="var(--icon)"/>
    <path d="M12 48 H108 L98 86 H22 Z" fill="var(--icon)"/>
    <g fill="var(--paper)">
      <circle cx="46" cy="58" r="4.5"/><circle cx="60" cy="58" r="4.5"/><circle cx="74" cy="58" r="4.5"/>
      <circle cx="46" cy="72" r="4.5"/><circle cx="60" cy="72" r="4.5"/><circle cx="74" cy="72" r="4.5"/>
    </g>
  </svg>

  <p class="story" style="left:888px; top:303px">then 2 more (and even<br>tweets about how<br>great your service is)…</p>
  <div class="icon icon-placeholder" role="img" aria-label="Social media post icon"
       style="left:800px; top:478px; width:115px; height:115px; background: radial-gradient(circle, #a0a0a0, #6a6a6a);"></div>

  <p class="story" style="left:888px; top:654px">and continues to make<br>purchases on a<br>bi-monthly basis</p>
  <svg class="icon cart-icon" viewBox="0 0 120 100" style="left:802px; top:834px; width:130px; height:108px" aria-label="Shopping cart" role="img">
    <path d="M4 10 H20 L36 70 H104" fill="none" stroke="var(--icon)" stroke-width="6" stroke-linecap="round" stroke-linejoin="round"/>
    <path d="M24 22 H114 L104 60 H34 Z" fill="var(--icon)"/>
    <g fill="var(--paper)">
      <circle cx="40" cy="33" r="5"/><circle cx="56" cy="33" r="5"/><circle cx="72" cy="33" r="5"/><circle cx="88" cy="33" r="5"/><circle cx="104" cy="33" r="5"/>
      <circle cx="46" cy="49" r="5"/><circle cx="62" cy="49" r="5"/><circle cx="78" cy="49" r="5"/><circle cx="94" cy="49" r="5"/>
    </g>
    <circle cx="44" cy="86" r="8" fill="var(--icon)"/><circle cx="96" cy="86" r="8" fill="var(--icon)"/>
  </svg>

  <div class="verdict">but really it is Kevin.</div>
</main>
</body>
</html>
```